Create modern and sleek business card for luxury real estate company

We're a "boutique" real estate office looking for a design that gets across a highly modern luxury brand. Blacks and whites are probably the best colors unless we try a silver foil for the logo. I've attached a version of our current logo here. I'd like to swap out the current font on there with Gotham Light Regular.

I'm looking to have one side of the card have the logo with the space for our agents info on the other side.

Target Market(s)

Young professionals in a "luxury" headspace

Industry/Entity Type

Real estate

Contact Information for Business Card

A place for agent name, cell number, website. The slogan "Quietly Redefining Fine Homes".

Font styles to use
Other font styles liked:
• Gotham Regular

Colors

Designer to choose only greyscale colors for use in the design.

Requirements
Must have
• Matte black as the background color. Clean lines and use of contrast. A specific design aspect that will use silver foil.
Nice to have
• Up in the air on integrating a QR code
Should not have
• Any houses or other real estate related design (ex: a clip art house)

```html
<!DOCTYPE html>
<html lang="en">
<head>
<meta charset="utf-8">
<title>Halden Realty – Business Card</title>
<link rel="stylesheet" href="https://fonts.googleapis.com/css2?family=Open+Sans:wght@400;600;700&display=swap">
<style>
  :root {
    --page: #e9e6e2;
    --card-black: #1c1b1a;
    --card-black-soft: #2b2927;
    --card-clear: #d9d5cf;
    --ink-dark: #232120;
    --text-warm: #cbbfb1;
    --text-muted: #9a8f84;
    --text-silver: #d7d3ce;
    --rule: #8a8178;
  }
  html, body {
    margin: 0;
    width: 1200px;
    height: 1200px;
    overflow: hidden;
    background: var(--page);
    font-family: "Open Sans", Arial, sans-serif;
  }
  .canvas {
    position: relative;
    width: 1200px;
    height: 1200px;
  }
  .card {
    position: absolute;
    left: 80px;
    top: 317px;
    width: 1040px;
    height: 566px;
    border-radius: 22px;
    overflow: hidden;
    background: var(--card-clear);
    box-shadow: 0 10px 30px rgba(0,0,0,0.15);
  }
  .card-shape {
    position: absolute;
    inset: 0;
  }
  .brand {
    position: absolute;
    left: 55px;
    top: 48px;
    display: flex;
    align-items: center;
    gap: 24px;
  }
  .brand-dot {
    width: 96px;
    height: 96px;
    border-radius: 50%;
    border: 3px solid var(--text-silver);
    box-sizing: border-box;
  }
  .brand-name {
    color: var(--text-silver);
    font-weight: 400;
    font-size: 42px;
    line-height: 1.08;
    letter-spacing: 2px;
  }
  .agent {
    position: absolute;
    left: 50px;
    top: 206px;
    width: 440px;
  }
  .agent-name {
    margin: 0;
    color: var(--text-warm);
    font-weight: 700;
    font-size: 33px;
    letter-spacing: 0.5px;
  }
  .agent-title {
    margin: 4px 0 0;
    color: var(--text-muted);
    font-size: 24px;
  }
  .rule {
    width: 71px;
    height: 2px;
    background: var(--rule);
    margin: 28px 0 24px;
  }
  .contact {
    list-style: none;
    margin: 0;
    padding: 0;
  }
  .contact li {
    display: flex;
    align-items: center;
    gap: 10px;
    color: var(--text-warm);
    font-size: 24px;
    height: 36.5px;
  }
  .contact svg {
    width: 20px;
    height: 20px;
    fill: var(--text-muted);
    flex: none;
  }
  .slogan {
    margin: 0;
    color: var(--text-warm);
    font-size: 25px;
    white-space: nowrap;
  }
</style>
</head>
<body>
<div class="canvas">
  <div class="card">
    <svg class="card-shape" viewBox="0 0 1040 566" width="1040" height="566" aria-hidden="true">
      <defs>
        <linearGradient id="matte" x1="0" y1="0" x2="1" y2="1">
          <stop offset="0" stop-color="#2b2927"/>
          <stop offset="0.6" stop-color="#1c1b1a"/>
          <stop offset="1" stop-color="#141312"/>
        </linearGradient>
      </defs>
      <rect class="black-panel" x="0" y="0" width="1040" height="566" fill="url(#matte)"/>
      <circle class="clear-window" cx="762" cy="290" r="305" fill="var(--card-clear)"/>
      <rect class="clear-edge" x="762" y="0" width="278" height="566" fill="var(--card-clear)"/>
      <circle class="mark-ring" cx="752" cy="290" r="250" fill="none" stroke="var(--ink-dark)" stroke-width="7"/>
      <text class="mark-name" x="752" y="306" text-anchor="middle" font-family="Open Sans, Arial, sans-serif" font-size="54" font-weight="400" letter-spacing="4" fill="var(--ink-dark)">HALDEN</text>
    </svg>

    <div class="brand">
      <div class="brand-dot"></div>
      <div class="brand-name">HALDEN<br>REALTY</div>
    </div>

    <div class="agent">
      <h1 class="agent-name">DANIEL REYES</h1>
      <p class="agent-title">President</p>
      <div class="rule"></div>
      <ul class="contact">
        <li><svg viewBox="0 0 24 24"><path d="M6.6 10.8a15.1 15.1 0 0 0 6.6 6.6l2.2-2.2a1 1 0 0 1 1-.25 11.4 11.4 0 0 0 3.6.57 1 1 0 0 1 1 1V20a1 1 0 0 1-1 1A17 17 0 0 1 3 4a1 1 0 0 1 1-1h3.5a1 1 0 0 1 1 1c0 1.25.2 2.45.57 3.57a1 1 0 0 1-.25 1z"/></svg>555-014-2290</li>
        <li><svg viewBox="0 0 24 24"><path d="M2 5h20v14H2z M3 6l9 7 9-7" /></svg>hello@haldenrealty.com</li>
        <li><svg viewBox="0 0 24 24"><path d="M12 2a10 10 0 1 0 0 20 10 10 0 0 0 0-20zm-1 17.9A8 8 0 0 1 4.1 11H8a14 14 0 0 0 3 8.9zM13 4.1A8 8 0 0 1 19.9 11H16a14 14 0 0 0-3-6.9zM10 11a12 12 0 0 1 2-6 12 12 0 0 1 2 6zm0 2h4a12 12 0 0 1-2 6 12 12 0 0 1-2-6z"/></svg>www.haldenrealty.com</li>
      </ul>
      <div class="rule"></div>
      <p class="slogan">Quietly Redefining Fine Homes</p>
    </div>
  </div>
</div>
</body>
</html>
```